Website for new slot-booking/reservations website/software

For a new software product we need a brand new logo and website for a reservations/booking system. The website should ideally present the main features with information text, contact info, news page as well as registration and pricing pages. As currently primary field of operation the software should be used for tennis but later on, also for other sport types. Also we'd like to be the logo a text-brand which includes the name "zeitfeldo.com" or just "zeitfeldo". The logo should ideally include an icon-design in some way. Generally we are open for ideas.

Bootstrap 4 template is a minimum requirement. (Multi-Page preferred, Single-Page still OK.)

You can use the attached image as an inspiration, but change of colors or other design elements are up to you. Currently the application has a primary color of #5500ff. The website created by you will not include the application itself, so it can have different (but ideally similar) Look&Feel.
Updates

Target Market(s)

Sports, Club-Management

Logo Text

zeitfeldo.com

Coding

Coded - Design and coding required

Number of Pages Required

5+ page

Font styles to use
Sans Serif

Requirements
Must have
• Bootstrap 4 Template, SCSS
Nice to have
• Rapid Loading Times, not too much external JS Libraries.
Should not have
• Extensive animations

```html
<!DOCTYPE html>
<html lang="en">
<head>
<meta charset="utf-8">
<title>zeitfeldo</title>
<link href="https://fonts.googleapis.com/css2?family=Montserrat:wght@400;500;600;700;800&display=swap" rel="stylesheet">
<style>
:root{
  --brand:#5500ff;
  --brand-deep:#3a0fd6;
  --brand-bright:#4a2bff;
  --ink:#1d1b2a;
  --text:#6a6878;
  --muted:#9c9aa8;
  --lavender:#f1eefb;
  --line:#dcd8ec;
  --white:#ffffff;
}
*{box-sizing:border-box;margin:0;padding:0}
html,body{width:1200px;height:3576px;overflow:hidden}
body{font-family:"Montserrat",Arial,sans-serif;color:var(--ink);background:var(--white);position:relative}
section,header,footer{position:absolute;left:0;width:1200px}
.btn{display:inline-block;border-radius:28px;font-weight:700;font-size:15px;letter-spacing:.5px;text-transform:uppercase;text-align:center;line-height:56px;height:56px}
.btn-light{background:var(--white);color:var(--brand)}
.btn-brand{background:var(--brand);color:var(--white)}
.section-title{font-size:44px;font-weight:700;text-align:center;letter-spacing:1px}

/* hero */
.hero{top:0;height:900px;background:radial-gradient(ellipse at 50% 40%,#5a3cff 0%,var(--brand) 45%,#4400e0 100%);overflow:hidden}
.nav{position:absolute;top:28px;left:140px;right:140px;height:56px;display:flex;align-items:center;z-index:2}
.logo{color:var(--white);font-weight:700;font-size:36px;letter-spacing:.5px}
.menu{margin-left:auto;display:flex;gap:24px;font-size:14px;font-weight:600;color:var(--white)}
.menu .active{border-bottom:2px solid var(--white);padding-bottom:4px}
.nav-cta{margin-left:36px;height:44px;line-height:44px;width:160px;font-size:13px}
.hero h1{position:absolute;top:165px;width:100%;text-align:center;color:var(--white);font-size:66px;font-weight:800;letter-spacing:2px}
.hero .lead{position:absolute;top:268px;width:100%;text-align:center;color:var(--white);font-size:23px;font-weight:600}
.hero-cta{position:absolute;top:320px;left:508px;width:184px}
.hero-wave{position:absolute;left:0;bottom:0}
.laptop{position:absolute;left:300px;top:450px;width:600px;height:380px}
.screen{position:absolute;left:28px;top:0;width:544px;height:340px;background:#2b2b33;border-radius:14px;padding:14px}
.screen-fill{width:100%;height:100%;border-radius:4px;background:linear-gradient(135deg,#f4f3fb 0%,#e3e0f6 55%,#c8c1f2 100%)}
.base{position:absolute;left:0;top:340px;width:600px;height:22px;background:linear-gradient(#d8d8de,#a9a9b2);border-radius:0 0 30px 30px}

/* features */
.features{top:900px;height:680px}
.features .section-title{position:absolute;top:60px;width:100%}
.feature-grid{position:absolute;top:170px;left:130px;width:940px;display:grid;grid-template-columns:repeat(3,1fr);row-gap:84px;column-gap:40px}
.feature{display:flex;gap:22px}
.feature-icon{flex:none;width:62px;height:62px;border-radius:50%;background:var(--white);box-shadow:0 6px 18px rgba(85,0,255,.15);display:flex;align-items:center;justify-content:center}
.feature h3{font-size:14px;font-weight:700;margin:6px 0 10px;letter-spacing:.3px}
.feature p{font-size:12px;line-height:19px;color:var(--text)}
.features .btn{position:absolute;top:515px;left:508px;width:184px}

/* about */
.about{top:1500px;height:700px;background:var(--lavender)}
.about-wave{position:absolute;top:0;left:0}
.about h2{position:absolute;top:170px;left:140px;font-size:44px;font-weight:700;line-height:54px;letter-spacing:1px}
.about p{position:absolute;top:300px;left:140px;width:440px;font-size:13px;line-height:22px;color:var(--text)}
.about .btn{position:absolute;top:530px;left:140px;width:184px}
.about-visual{position:absolute;top:200px;left:610px;width:540px;height:370px;border-radius:10px;background:linear-gradient(135deg,#ffffff 0%,#d9d3f4 50%,#b8acef 100%)}

/* news */
.news{top:2200px;height:430px}
.news .section-title{position:absolute;top:60px;width:100%}
.news-cards{position:absolute;top:150px;left:140px;width:920px;display:flex;gap:40px}
.card{width:280px;height:230px;background:var(--white);border:1px solid var(--line);box-shadow:0 4px 18px rgba(40,20,90,.08);padding:26px 20px}
.card-head{display:flex;gap:12px}
.date{flex:none;width:46px;height:50px;background:var(--brand);color:var(--white);text-align:center;font-weight:700;font-size:17px;padding-top:6px;line-height:18px}
.date small{display:block;font-size:10px}
.card h4{font-size:13px;font-weight:700;line-height:20px;padding-top:4px}
.card p{margin-top:18px;font-size:12px;line-height:19px;color:var(--text)}
.card .more{display:block;margin-top:20px;font-size:12px;font-weight:700;color:var(--brand)}
.arrow{position:absolute;top:240px}

/* contact */
.contact{top:2600px;height:700px;background:radial-gradient(ellipse at 50% 50%,#5a3cff 0%,var(--brand) 55%,#4400e0 100%);overflow:hidden}
.contact-wave{position:absolute;top:0;left:0}
.contact .section-title{position:absolute;top:185px;width:100%;color:var(--white)}
.form{position:absolute;top:310px;left:170px;width:860px}
.row{display:flex;gap:20px}
.field{flex:1;height:40px;border:1px solid rgba(255,255,255,.45);border-radius:4px;color:var(--white);font-size:13px;padding:11px 14px}
.message{margin-top:20px;height:130px;flex:none;width:100%}
.contact .btn{position:absolute;top:535px;left:492px;width:216px}

/* footer */
.footer{top:3300px;height:276px;background:var(--white)}
.contact-row{position:absolute;top:40px;left:240px;width:720px;display:flex;justify-content:space-between;align-items:center;font-size:13px;color:var(--ink)}
.contact-item{display:flex;align-items:center;gap:14px}
.contact-item .ic{width:40px;height:40px;border-radius:50%;border:1px solid var(--line);display:flex;align-items:center;justify-content:center}
.foot-menu{position:absolute;top:130px;width:100%;display:flex;justify-content:center;gap:40px;font-size:20px;font-weight:600}
.copy{position:absolute;top:180px;width:100%;text-align:center;font-size:11px;color:var(--muted)}
.social{position:absolute;top:212px;width:100%;display:flex;justify-content:center;gap:8px}
.social span{width:26px;height:26px;border-radius:50%;background:var(--brand)}
</style>
</head>
<body>

<header class="hero">
  <nav class="nav">
    <span class="logo">zeitfeldo</span>
    <div class="menu">
      <span class="active">HOME</span><span>FEATURES</span><span>CONTACT</span><span>NEWS</span><span>PRICING</span>
    </div>
    <span class="btn btn-light nav-cta">Registration</span>
  </nav>
  <h1>ZEITFELDO</h1>
  <p class="lead">Sed ut perspiciatis unde omnis isvoluptatem accusantium</p>
  <span class="btn btn-light hero-cta">Booking Now</span>

  <svg class="hero-wave" width="1200" height="360" viewBox="0 0 1200 360">
    <path d="M0 250 C 300 170 800 140 1200 40 L1200 360 L0 360Z" fill="#7b5cff" opacity=".55"/>
    <path d="M0 300 C 350 230 850 230 1200 110 L1200 360 L0 360Z" fill="#b9a6ff" opacity=".7"/>
    <path d="M0 340 C 400 290 850 300 1200 190 L1200 360 L0 360Z" fill="#ffffff"/>
  </svg>

  <div class="laptop">
    <div class="screen"><div class="screen-fill" role="img" aria-label="Booking dashboard screenshot with charts and calendar"></div></div>
    <div class="base"></div>
  </div>
</header>

<section class="features">
  <h2 class="section-title">OUR FEATURES</h2>
  <div class="feature-grid">
    <div class="feature">
      <div class="feature-icon"><svg width="26" height="26" viewBox="0 0 26 26" fill="none" stroke="#5500ff" stroke-width="2"><rect x="3" y="6" width="20" height="14" rx="2"/><path d="M3 11h20"/></svg></div>
      <div><h3>SEO UT PERSPICIATIS</h3><p>Lorem ipsum dolor sit amet consectetur adipiscing elit sed tempor incididunt ut labore magna.</p></div>
    </div>
    <div class="feature">
      <div class="feature-icon"><svg width="26" height="26" viewBox="0 0 26 26" fill="none" stroke="#5500ff" stroke-width="2"><rect x="7" y="3" width="12" height="20" rx="2"/><path d="M11 19h4"/></svg></div>
      <div><h3>QUIS AUTE IRURE</h3><p>Lorem ipsum dolor sit amet consectetur adipiscing elit sed tempor incididunt ut labore magna.</p></div>
    </div>
    <div class="feature">
      <div class="feature-icon"><svg width="26" height="26" viewBox="0 0 26 26" fill="none" stroke="#5500ff" stroke-width="2"><rect x="4" y="4" width="18" height="18" rx="2"/><path d="M13 4v18M4 13h18"/></svg></div>
      <div><h3>REPREHENDERIT</h3><p>Lorem ipsum dolor sit amet consectetur adipiscing elit sed tempor incididunt ut labore magna.</p></div>
    </div>
    <div class="feature">
      <div class="feature-icon"><svg width="26" height="26" viewBox="0 0 26 26" fill="none" stroke="#5500ff" stroke-width="2"><rect x="5" y="11" width="16" height="12" rx="2"/><path d="M9 11V8a4 4 0 0 1 8 0v3"/></svg></div>
      <div><h3>QUIS NOSTRUM</h3><p>Lorem ipsum dolor sit amet consectetur adipiscing elit sed tempor incididunt ut labore magna.</p></div>
    </div>
    <div class="feature">
      <div class="feature-icon"><svg width="26" height="26" viewBox="0 0 26 26" fill="none" stroke="#5500ff" stroke-width="2"><path d="M8 4h10l3 4-8 14L5 8z"/><path d="M5 8h16"/></svg></div>
      <div><h3>VOLUPTATEM</h3><p>Lorem ipsum dolor sit amet consectetur adipiscing elit sed tempor incididunt ut labore magna.</p></div>
    </div>
    <div class="feature">
      <div class="feature-icon"><svg width="26" height="26" viewBox="0 0 26 26" fill="none" stroke="#5500ff" stroke-width="2"><rect x="3" y="5" width="20" height="15" rx="2"/><path d="M3 9l10 6 10-6"/></svg></div>
      <div><h3>EXERCITATIONEM</h3><p>Lorem ipsum dolor sit amet consectetur adipiscing elit sed tempor incididunt ut labore magna.</p></div>
    </div>
  </div>
  <span class="btn btn-brand">View More</span>
</section>

<section class="about">
  <svg class="about-wave" width="1200" height="90" viewBox="0 0 1200 90">
    <path d="M0 0 H1200 V40 C1140 70 1080 70 1020 40 C960 10 900 10 840 40 C780 70 720 70 660 40 C600 10 540 10 480 40 C420 70 360 70 300 40 C240 10 180 10 120 40 C60 70 30 60 0 40Z" fill="#ffffff"/>
  </svg>
  <h2>ABOUT<br>ZEITFELDO</h2>
  <p>Lorem ipsum dolor sit amet, consectetur adipiscing elit sed do eiusmod tempor incididunt ut labore et dolore magna aliqua. Ut enim ad minim veniam, quis nostrud exercitation ullamco laboris nisi ut aliquip ex ea commodo consequat. Duis aute irure dolor in reprehenderit in voluptate velit esse cillum dolore eu fugiat nulla pariatur. Excepteur sint occaecat cupidatat non proident, sunt in culpa qui officia deserunt mollit anim id est laborum sed ut perspiciatis.</p>
  <span class="btn btn-brand">Read More</span>
  <div class="about-visual" role="img" aria-label="Desktop monitors showing the booking software, with a faint tennis player in the background"></div>
</section>

<section class="news">
  <h2 class="section-title">LATEST NEWS</h2>
  <svg class="arrow" style="left:60px" width="20" height="40" viewBox="0 0 20 40"><path d="M16 4 4 20l12 16" fill="none" stroke="#c9c5d8" stroke-width="2"/></svg>
  <svg class="arrow" style="right:60px" width="20" height="40" viewBox="0 0 20 40"><path d="M4 4l12 16L4 36" fill="none" stroke="#c9c5d8" stroke-width="2"/></svg>
  <div class="news-cards">
    <article class="card">
      <div class="card-head"><div class="date">02<small>JAN</small></div><h4>Pellentesque faucibus Ut accumsan ultric</h4></div>
      <p>Lorem ipsum dolor sit amet consectetur adipiscing elit, sed do eiusmod tempor incididunt labore.</p>
      <span class="more">READ MORE</span>
    </article>
    <article class="card">
      <div class="card-head"><div class="date">02<small>JAN</small></div><h4>Pellentesque faucibus Ut accumsan ultric</h4></div>
      <p>Lorem ipsum dolor sit amet consectetur adipiscing elit, sed do eiusmod tempor incididunt labore.</p>
      <span class="more">READ MORE</span>
    </article>
    <article class="card">
      <div class="card-head"><div class="date">02<small>JAN</small></div><h4>Pellentesque faucibus Ut accumsan ultric</h4></div>
      <p>Lorem ipsum dolor sit amet consectetur adipiscing elit, sed do eiusmod tempor incididunt labore.</p>
      <span class="more">READ MORE</span>
    </article>
  </div>
</section>

<section class="contact">
  <svg class="contact-wave" width="1200" height="110" viewBox="0 0 1200 110">
    <path d="M0 0 H1200 V60 C1140 95 1080 95 1020 60 C960 25 900 25 840 60 C780 95 720 95 660 60 C600 25 540 25 480 60 C420 95 360 95 300 60 C240 25 180 25 120 60 C60 95 30 85 0 60Z" fill="#d9d2ff" opacity=".6"/>
    <path d="M0 0 H1200 V40 C1140 75 1080 75 1020 40 C960 5 900 5 840 40 C780 75 720 75 660 40 C600 5 540 5 480 40 C420 75 360 75 300 40 C240 5 180 5 120 40 C60 75 30 65 0 40Z" fill="#ffffff"/>
  </svg>
  <h2 class="section-title">CONTACT FORM</h2>
  <div class="form">
    <div class="row">
      <div class="field">Enter Name</div>
      <div class="field">Enter Email</div>
      <div class="field">Enter Phone</div>
    </div>
    <div class="field message">Message</div>
  </div>
  <span class="btn btn-light">Submit Message</span>
</section>

<footer class="footer">
  <div class="contact-row">
    <div class="contact-item">
      <span class="ic"><svg width="16" height="16" viewBox="0 0 16 16" fill="none" stroke="#5500ff" stroke-width="1.6"><path d="M8 15s5-5 5-8.5A5 5 0 0 0 3 6.5C3 10 8 15 8 15z"/><circle cx="8" cy="6.5" r="1.8"/></svg></span>
      <span>203 Sed ut perspiciatis unde<br>omnis iste natus error</span>
    </div>
    <div class="contact-item">
      <span class="ic"><svg width="16" height="16" viewBox="0 0 16 16" fill="none" stroke="#5500ff" stroke-width="1.6"><path d="M4 2h3l1 3-2 1a8 8 0 0 0 4 4l1-2 3 1v3a1 1 0 0 1-1 1A12 12 0 0 1 3 3a1 1 0 0 1 1-1z"/></svg></span>
      <span>1 800 555 0147</span>
    </div>
    <div class="contact-item">
      <span class="ic"><svg width="16" height="16" viewBox="0 0 16 16" fill="none" stroke="#5500ff" stroke-width="1.6"><rect x="2" y="3.5" width="12" height="9" rx="1"/><path d="M2 4.5l6 4 6-4"/></svg></span>
      <span>info@zeitfeldo.com</span>
    </div>
  </div>
  <div class="foot-menu"><span>HOME</span><span>FEATURES</span><span>CONTACT</span><span>NEWS</span><span>PRICING</span></div>
  <p class="copy">Copyright 2020 zeitfeldo All Rights Reserved | Privacy Policy</p>
  <div class="social"><span></span><span></span><span></span></div>
</footer>

</body>
</html>
```